Business Card - Business Consultancy

Newly Established Company, specializing in Business Consultancy, Human Resource Management, Talent Acquisition and Payroll Solutions.

We need a Business card design which portrays "elegance" and a very sleek yet business-like design. We would like a nice blue trimming (which goes well with the logo) to separate the content of the business card at the top. We would also like to see the design using the color silver either as a background or incorporated into it.

The final design should be a Business card which has colors matching the logo; a nice font; the above-mentioned specifics that adheres to the theme of "a stylish and professional business"

FYI: please do not have too fanciful designs.

Industry/Entity Type

Business Consultant

Contact Information for Business Card

Darren Lim
Business Development Director
Arbor Talent Consulting Private Limited
27 Wexley Street, #05-03B
Harbourgate Trade Building
Singapore 059317
Mobile : (+65) 98354417
Email : dlim@arbortalent-advisory.com
Alternative : arbortalentadvisory@mailbox-example.com

Requirements
Must have
• Nice Blue Trimming matching Logo which separates content, see attached
• Design incorporates either a silver background or the use of the color silver
Should not have
• No Fanciful Designs
• No Childish Designs
• No Overly Complicated Designs

```html
<!DOCTYPE html>
<html lang="en">
<head>
<meta charset="utf-8">
<title>Arbor Talent Consulting – Business Card</title>
<link rel="stylesheet" href="https://fonts.googleapis.com/css2?family=Open+Sans:wght@400;600;700&family=Lato:wght@400&display=swap">
<style>
  :root {
    --stage-top: #2a2a2a;
    --stage-bottom: #050505;
    --silver-light: #f6f7f8;
    --silver-mid: #e4e6e9;
    --silver-deep: #c9cdd2;
    --card-white: #ffffff;
    --brand-blue: #1a7cc4;
    --brand-blue-light: #5aa9e0;
    --ink: #1c1c1c;
  }
  * { margin: 0; padding: 0; box-sizing: border-box; }
  html, body { width: 1200px; height: 900px; overflow: hidden; }
  body {
    position: relative;
    background: linear-gradient(180deg, var(--stage-top) 0%, var(--stage-bottom) 100%);
    font-family: "Lato", sans-serif;
    color: var(--ink);
  }
  .card {
    position: absolute;
    top: 184px;
    height: 490px;
    border-radius: 12px;
    text-align: center;
    overflow: hidden;
  }
  .card-front {
    left: 299px; width: 301px;
    background: linear-gradient(160deg, var(--silver-light) 0%, var(--silver-mid) 55%, var(--silver-deep) 100%);
  }
  .card-back {
    left: 645px; width: 305px;
    background: linear-gradient(180deg, var(--card-white) 0%, var(--card-white) 80%, var(--silver-mid) 100%);
  }

  .brand {
    position: absolute;
    top: 44px;
    left: 0;
    width: 100%;
    display: flex;
    align-items: center;
    justify-content: center;
    gap: 12px;
  }
  .brand-dot {
    width: 46px; height: 46px;
    border-radius: 50%;
    background: var(--brand-blue);
  }
  .brand-name {
    font-family: "Open Sans", sans-serif;
    font-weight: 700;
    font-size: 19px;
    line-height: 1.15;
    color: var(--brand-blue);
    text-align: left;
  }

  .trim {
    position: absolute;
    left: 0; width: 100%;
    height: 4px;
    background: linear-gradient(90deg, var(--brand-blue) 0%, var(--brand-blue-light) 100%);
  }
  .trim-front { top: 132px; }
  .trim-front::after {
    content: "";
    position: absolute; left: 0; top: 6px;
    width: 100%; height: 1px;
    background: var(--silver-deep);
  }
  .trim-back { bottom: 0; height: 6px; }

  .holder { position: absolute; top: 241px; left: 0; width: 100%; }
  .holder-name {
    font-family: "Open Sans", sans-serif;
    font-weight: 600;
    font-size: 18px;
    color: var(--brand-blue);
    line-height: 24px;
  }
  .holder-title { font-size: 14px; line-height: 18px; }

  .address {
    position: absolute; top: 306px; left: 0; width: 100%;
    font-style: normal;
    font-size: 14px; line-height: 21px;
  }
  .contacts {
    position: absolute; top: 396px; left: 0; width: 100%;
    font-size: 13.5px; line-height: 20px;
    list-style: none;
  }
  .contacts li { display: flex; align-items: center; justify-content: center; gap: 4px; }
  .contacts svg { width: 10px; height: 10px; flex: none; }
  .icon-phone { fill: var(--brand-blue); }
  .icon-mail rect { fill: var(--brand-blue); }
  .icon-mail path { fill: none; stroke: #ffffff; stroke-width: 2; }

  .back-mark {
    position: absolute; top: 170px; left: 50%;
    width: 130px; height: 130px; margin-left: -65px;
    border-radius: 50%;
    background: var(--brand-blue);
  }
  .back-name {
    position: absolute; top: 314px; left: 0; width: 100%;
    font-family: "Open Sans", sans-serif;
    font-weight: 700; font-size: 17px;
    color: var(--brand-blue);
  }
  .services {
    position: absolute; top: 349px; left: 14px; right: 14px;
    font-family: "Open Sans", sans-serif;
    font-weight: 600; font-size: 15px; line-height: 21px;
    color: var(--brand-blue);
  }
</style>
</head>
<body>
  <section class="card card-front">
    <div class="brand">
      <span class="brand-dot"></span>
      <span class="brand-name">Arbor Talent<br>Consulting</span>
    </div>
    <span class="trim trim-front"></span>
    <div class="holder">
      <p class="holder-name">Darren Lim</p>
      <p class="holder-title">Business Development Director</p>
    </div>
    <address class="address">
      27 Wexley Street, #05-03B<br>
      Harbourgate Trade Building<br>
      Singapore 059317
    </address>
    <ul class="contacts">
      <li><svg class="icon-phone" viewBox="0 0 24 24" aria-hidden="true"><path d="M6.6 10.8a15.1 15.1 0 0 0 6.6 6.6l2.2-2.2a1 1 0 0 1 1-.25 11.4 11.4 0 0 0 3.6.57 1 1 0 0 1 1 1V20a1 1 0 0 1-1 1A17 17 0 0 1 3 4a1 1 0 0 1 1-1h3.5a1 1 0 0 1 1 1c0 1.25.2 2.45.57 3.57a1 1 0 0 1-.25 1z"/></svg>(+65) 98354417</li>
      <li><svg class="icon-mail" viewBox="0 0 24 24" aria-hidden="true"><rect x="1" y="4" width="22" height="16" rx="1"/><path d="M2 5l10 8 10-8"/></svg>dlim@arbortalent-advisory.com</li>
      <li><svg class="icon-mail" viewBox="0 0 24 24" aria-hidden="true"><rect x="1" y="4" width="22" height="16" rx="1"/><path d="M2 5l10 8 10-8"/></svg>arbortalentadvisory@mailbox-example.com</li>
    </ul>
  </section>

  <section class="card card-back">
    <span class="back-mark"></span>
    <p class="back-name">Arbor Talent Consulting</p>
    <p class="services">Recruitment | HR Solutions | Business Consultancy</p>
    <span class="trim trim-back"></span>
  </section>
</body>
</html>
```